I need a website designed. I am a mortgage loan officer and would like to have a website for me and my team where i can post resources, videos and blog information for my clients. A website like themorvaskteam.com .

The theme is - The Pelkins Team - Home Loan Group powered by Brightwell Home Loans -

Target Market(s)

B2B (Real Estate Agents)and B2C (Home buyers and refinancing)

Industry/Entity Type

Mortgage Lender

Coding

Coded - Design and coding required

Number of Pages Required

5+ page

Font styles to use
Serif
Sans Serif

Colors

Designer to choose colors to be used in the design.

Requirements
Must have
• Disclaimers: Licensed by the Bureau of Lending Affairs under the Pacific Credit Providers Act. Loans made or arranged pursuant to a Pacific Credit Providers Act License. Equal Housing Lender Brightwell Cannot Accept mortgage applications for properties located in New York via this site
• Mobile Friendly
Nice to have
• Main Links: Home, About Us(see team flyer), Mortgage 101, Contact Us (formzig form)

```html
<!DOCTYPE html>
<html lang="en">
<head>
<meta charset="utf-8">
<title>The Pelkins Team – Home Loan Group</title>
<link href="https://fonts.googleapis.com/css2?family=Raleway:wght@500;600;700&family=Open+Sans:wght@400;600;700&display=swap" rel="stylesheet">
<style>
:root{
  --blue:#0b66c2;
  --blue-dark:#0a58a8;
  --navy:#1f3a66;
  --ink:#222831;
  --text:#5a5f66;
  --muted:#8a9099;
  --line:#d5d8dc;
  --white:#ffffff;
  --footer:#0a64bf;
}
*{margin:0;padding:0;box-sizing:border-box}
html,body{width:1200px;height:3629px;overflow:hidden}
body{position:relative;background:var(--white);font-family:"Open Sans",Arial,sans-serif;color:var(--text)}
.abs{position:absolute}
.h-title{font-family:"Raleway",Arial,sans-serif;font-weight:700;color:var(--ink);text-align:center;font-size:30px;letter-spacing:.5px;width:1200px;left:0}
.divider{position:absolute;left:360px;width:480px;height:20px}
.photo{position:absolute}
.btn{position:absolute;display:flex;align-items:center;justify-content:center;font-weight:600;font-size:13px;color:var(--white);background:var(--blue);letter-spacing:.4px}
/* header */
.site-header{position:absolute;top:0;left:0;width:1200px;height:108px;background:rgba(255,255,255,.88);z-index:3}
.brand{position:absolute;left:116px;top:38px;display:flex;align-items:center;gap:12px;font-family:"Raleway",Arial,sans-serif;font-weight:700;font-size:30px;color:var(--navy)}
.brand-mark{width:22px;height:22px;background:var(--navy)}
.nav a{position:absolute;top:44px;font-family:"Raleway",Arial,sans-serif;font-weight:600;font-size:17px;color:#555b63;text-decoration:none}
.nav a.active{color:var(--blue)}
/* hero */
.hero{position:absolute;top:0;left:0;width:1200px;height:714px;overflow:hidden}
.hero-photo{position:absolute;inset:0;background:linear-gradient(180deg,#6d7f9a 0%,#5b5f68 35%,#6a5b4a 65%,#3c4a2e 100%)}
.hero-title{top:292px;font-family:"Raleway",Arial,sans-serif;font-weight:600;font-size:56px;letter-spacing:4px;color:var(--white);text-align:center;width:1200px}
.hero-sub{top:360px;font-family:"Raleway",Arial,sans-serif;font-weight:600;font-size:30px;letter-spacing:3px;color:var(--white);text-align:center;width:1200px}
.arrow-circle{position:absolute;width:50px;height:50px;border:2px solid var(--white);border-radius:50%}
/* welcome */
.welcome-text{top:800px;left:190px;width:820px;text-align:center;font-size:14px;line-height:26px;color:var(--text)}
.btn-outline{position:absolute;left:516px;top:910px;width:170px;height:46px;border:2px solid var(--navy);color:var(--navy);font-weight:600;font-size:15px;display:flex;align-items:center;justify-content:center}
/* videos */
.videos{position:absolute;top:1036px;left:0;width:1200px;height:472px;background:linear-gradient(180deg,#5d6877 0%,#3d6596 55%,#0c6cc6 100%)}
.video-card{position:absolute;top:130px;width:426px;height:254px;border:8px solid var(--white)}
.white-title{color:var(--white)}
/* team */
.card{position:absolute;background:var(--white);border:2px solid #dcdfe3}
.avatar{position:absolute;border-radius:50%;border:3px solid var(--navy);background:radial-gradient(circle at 50% 40%,#9aa3ad,#4a5563)}
.name{font-family:"Raleway",Arial,sans-serif;font-weight:700;color:var(--ink)}
.role{color:var(--blue);font-weight:600}
.small-card .name{position:absolute;top:176px;width:100%;text-align:center;font-size:21px}
.small-card .role{position:absolute;top:202px;width:100%;text-align:center;font-size:13px}
.small-card p{position:absolute;top:230px;left:14px;right:14px;text-align:center;font-size:12px;line-height:20px}
/* resources */
.resources{position:absolute;top:2338px;left:0;width:1200px;height:445px;background:linear-gradient(180deg,#e6e8ea 0%,#cfd3d7 60%,#dfe2e5 100%)}
.res-card{position:absolute;top:140px;width:470px;height:211px;background:var(--white);box-shadow:0 2px 6px rgba(0,0,0,.12)}
.res-card h3{position:absolute;left:226px;top:22px;font-family:"Open Sans",Arial,sans-serif;font-weight:600;font-size:16px;color:var(--blue)}
.res-card p{position:absolute;left:226px;top:56px;width:220px;font-size:12.5px;line-height:20px}
.res-card .more{position:absolute;left:226px;top:162px;font-size:12px;font-weight:700;color:var(--ink)}
/* blogs */
.blog-card{position:absolute;background:var(--white);border:2px solid #dcdfe3}
.blog-card h4{font-family:"Raleway",Arial,sans-serif;font-weight:600;color:var(--ink)}
.blog-card p{font-size:11.5px;line-height:17px;color:var(--muted)}
/* footer */
.site-footer{position:absolute;top:3345px;left:0;width:1200px;height:284px;background:var(--footer);color:var(--white)}
.contact-item{position:absolute;top:42px;display:flex;align-items:center;gap:10px;font-size:15px;font-weight:600}
.foot-links a{position:absolute;top:120px;color:var(--white);text-decoration:none;font-size:13px;font-weight:600}
.social{position:absolute;top:110px;width:32px;height:32px;border:2px solid var(--white);border-radius:50%}
</style>
</head>
<body>

<header class="site-header">
  <div class="brand"><span class="brand-mark"></span>The Pelkins Team</div>
  <nav class="nav">
    <a class="active" style="left:588px">HOME</a>
    <a style="left:687px">ABOUT US</a>
    <a style="left:820px">MORTGAGE 101</a>
    <a style="left:995px">CONTACT US</a>
  </nav>
</header>

<section class="hero">
  <div class="hero-photo" role="img" aria-label="Large two-storey family home with lit windows at dusk"></div>
  <h1 class="abs hero-title">HOME LOAN CONSULTING</h1>
  <p class="abs hero-sub">MORBI ORNARE GRAVIDA INTEGER</p>
  <div class="btn" style="left:508px;top:408px;width:186px;height:50px;font-size:17px">LEARN MORE</div>
  <div class="arrow-circle" style="left:84px;top:326px"><svg width="46" height="46"><path d="M26 14 L17 23 L26 32" stroke="#fff" stroke-width="3" fill="none"/></svg></div>
  <div class="arrow-circle" style="left:1080px;top:326px"><svg width="46" height="46"><path d="M20 14 L29 23 L20 32" stroke="#fff" stroke-width="3" fill="none"/></svg></div>
  <svg class="abs" style="left:0;top:0" width="1200" height="714"><path d="M0 610 Q560 770 1200 560 L1200 714 L0 714 Z" fill="#fff"/></svg>
</section>

<section>
  <h2 class="abs h-title" style="top:724px">WELCOME TO THE PELKINS TEAM</h2>
  <svg class="divider" style="top:766px" viewBox="0 0 480 20"><line x1="0" y1="10" x2="480" y2="10" stroke="#c9cdd2"/><rect x="230" y="0" width="20" height="20" fill="#1f3a66"/></svg>
  <p class="abs welcome-text">elementum elit at tellus nec ultricies sit amet porttitor mattis enim In massa libero interdum nec interdum vel blandit sed nulla In ullamcorper est eget tempor cursus neque mi consectetuer mi a ultricies massa est sed nisl Class aptent taciti sociosqu ad litora torquent per conubia nostra per inceptos hymenaeos Proin nulla arcu nonummy</p>
  <div class="btn-outline">LEARN MORE</div>
</section>

<section class="videos">
  <h2 class="abs h-title white-title" style="top:26px">OUR VIDEOS</h2>
  <svg class="divider" style="top:68px" viewBox="0 0 480 20"><line x1="0" y1="10" x2="480" y2="10" stroke="#ffffff" stroke-opacity=".7"/><rect x="230" y="0" width="20" height="20" fill="#fff"/></svg>
  <div class="video-card" style="left:150px">
    <div class="photo" style="inset:0;background:linear-gradient(135deg,#d8d4cf,#8a7a6c 60%,#6b4a3a)" role="img" aria-label="Family walking into their new home"></div>
    <svg class="abs" style="left:165px;top:79px" width="80" height="80"><circle cx="40" cy="40" r="37" fill="none" stroke="#fff" stroke-width="4"/><path d="M32 24 L56 40 L32 56 Z" fill="#fff"/></svg>
  </div>
  <div class="video-card" style="left:627px">
    <div class="photo" style="inset:0;background:linear-gradient(135deg,#c9d3dc,#9fb0c0 55%,#6c7e92)" role="img" aria-label="Couple planning their finances"></div>
    <svg class="abs" style="left:165px;top:79px" width="80" height="80"><circle cx="40" cy="40" r="37" fill="none" stroke="#fff" stroke-width="4"/><path d="M32 24 L56 40 L32 56 Z" fill="#fff"/></svg>
  </div>
  <svg class="abs" style="left:86px;top:222px" width="24" height="36"><path d="M18 4 L6 18 L18 32" stroke="#fff" stroke-width="4" fill="none"/></svg>
  <svg class="abs" style="left:1084px;top:222px" width="24" height="36"><path d="M6 4 L18 18 L6 32" stroke="#fff" stroke-width="4" fill="none"/></svg>
</section>

<section>
  <h2 class="abs h-title" style="top:1542px">OUR TEAM</h2>
  <svg class="divider" style="top:1584px" viewBox="0 0 480 20"><line x1="0" y1="10" x2="480" y2="10" stroke="#c9cdd2"/><rect x="230" y="0" width="20" height="20" fill="#1f3a66"/></svg>

  <div class="card" style="left:128px;top:1660px;width:937px;height:235px">
    <div class="avatar" style="left:28px;top:26px;width:198px;height:198px" role="img" aria-label="Portrait of Owen Pelkins"></div>
    <div class="abs name" style="left:252px;top:50px;font-size:23px">OWEN PELKINS</div>
    <div class="abs role" style="left:252px;top:84px;font-size:14px">Producing Branch Manager</div>
    <p class="abs" style="left:252px;top:116px;width:660px;font-size:14px;line-height:26px">I have over 15 years of experience in Mortgage Planning. I rank in the top 1% of loan originators in the country. I pride myself on making the home buying process as smooth as possible. I will guide you through the mortgage process and look forward to helping you with your transaction</p>
  </div>

  <div class="card small-card" style="left:128px;top:1943px;width:303px;height:339px">
    <div class="avatar" style="left:81px;top:14px;width:138px;height:138px" role="img" aria-label="Portrait of Marco Ellison"></div>
    <div class="name">MARCO ELLISON</div><div class="role">Loan Partner</div>
    <p>I am able to help customers with pre-qualifications and pre-approvals and keep the applicants and real estate agents informed during the application process.</p>
  </div>
  <div class="card small-card" style="left:460px;top:1943px;width:285px;height:339px">
    <div class="avatar" style="left:72px;top:14px;width:138px;height:138px" role="img" aria-label="Portrait of Daniel Okafor"></div>
    <div class="name">DANIEL OKAFOR</div><div class="role">Loan Processor</div>
    <p>I am able to help customers with pre-qualifications and pre-approvals and keep the applicants and real estate agents informed during the application process.</p>
  </div>
  <div class="card small-card" style="left:765px;top:1943px;width:300px;height:339px">
    <div class="avatar" style="left:80px;top:14px;width:138px;height:138px" role="img" aria-label="Portrait of Laura Brenning"></div>
    <div class="name">LAURA BRENNING</div><div class="role">Closing Coordinator/Team Leader</div>
    <p>I am able to help customers with pre-qualifications and pre-approvals and keep the applicants and real estate agents informed during the application process.</p>
  </div>
</section>

<section class="resources" role="img" aria-label="Faded background of a suburban house">
  <h2 class="abs h-title" style="top:40px">RESOURCES</h2>
  <svg class="divider" style="top:82px" viewBox="0 0 480 20"><line x1="0" y1="10" x2="480" y2="10" stroke="#a9aeb4"/><rect x="230" y="0" width="20" height="20" fill="#1f3a66"/></svg>
  <div class="res-card" style="left:119px">
    <div class="photo" style="left:19px;top:17px;width:196px;height:175px;background:linear-gradient(135deg,#e8e2dc,#c2453f 55%,#8a6b58)" role="img" aria-label="Handshake over a model house and keys"></div>
    <h3>Elementum elit tellus</h3>
    <p>nec ultricies sit amet porttitor mattis enim In massa libero interdum nec interdum vel blandit sed nulla In ullamcorper est eget</p>
    <div class="more">READ MORE</div>
  </div>
  <div class="res-card" style="left:610px">
    <div class="photo" style="left:19px;top:17px;width:196px;height:175px;background:linear-gradient(135deg,#dcdcd6,#7a8a6a 50%,#3e4a3a)" role="img" aria-label="Laptop showing a home on screen"></div>
    <h3>Nam eget lacus Aliquam</h3>
    <p>nec ultricies sit amet porttitor mattis enim In massa libero interdum nec interdum vel blandit sed nulla In ullamcorper est eget</p>
    <div class="more">READ MORE</div>
  </div>
  <svg class="abs" style="left:78px;top:228px" width="20" height="30"><path d="M15 3 L5 15 L15 27" stroke="#fff" stroke-width="3" fill="none"/></svg>
  <svg class="abs" style="left:1100px;top:228px" width="20" height="30"><path d="M5 3 L15 15 L5 27" stroke="#fff" stroke-width="3" fill="none"/></svg>
</section>

<section>
  <h2 class="abs h-title" style="top:2820px">OUR BLOGS</h2>
  <svg class="divider" style="top:2862px" viewBox="0 0 480 20"><line x1="0" y1="10" x2="480" y2="10" stroke="#c9cdd2"/><rect x="230" y="0" width="20" height="20" fill="#1f3a66"/></svg>

  <div class="blog-card" style="left:128px;top:2928px;width:470px;height:344px">
    <div class="photo" style="left:0;top:0;width:466px;height:206px;background:linear-gradient(135deg,#3a4a5a,#6b7a88 50%,#a89478)" role="img" aria-label="Business handshake above a model house"></div>
    <h4 class="abs" style="left:20px;top:226px;font-size:17px">Etiam est nunc venenatis in tristique</h4>
    <p class="abs" style="left:20px;top:254px;width:420px">netus et malesuada fames ac turpis egestas Cras id elit Integer quis urna Ut ante enim dapibus malesuada fringilla eu condimen</p>
    <div class="btn" style="left:20px;top:292px;width:118px;height:32px;font-size:12px">READ MORE</div>
  </div>

  <div class="blog-card" style="left:615px;top:2928px;width:472px;height:165px">
    <div class="photo" style="left:0;top:0;width:220px;height:161px;background:linear-gradient(135deg,#8fa26a,#c9a888 60%,#6a7a4a)" role="img" aria-label="Hand passing a small model house and keys"></div>
    <h4 class="abs" style="left:240px;top:18px;font-size:17px">Blog Title here</h4>
    <p class="abs" style="left:240px;top:46px;width:210px">netus et malesuada fames ac turpis egestas Cras id elit Integer quis urna Ut ante enim dapibus malesuada</p>
    <div class="btn" style="left:240px;top:116px;width:118px;height:30px;font-size:12px">READ MORE</div>
  </div>
  <div class="blog-card" style="left:615px;top:3105px;width:472px;height:167px">
    <div class="photo" style="left:0;top:0;width:220px;height:163px;background:linear-gradient(135deg,#e9e4de,#c9b7a6 55%,#8a6e5a)" role="img" aria-label="Smiling couple reviewing documents"></div>
    <h4 class="abs" style="left:240px;top:18px;font-size:17px">Blog Title here</h4>
    <p class="abs" style="left:240px;top:46px;width:210px">netus et malesuada fames ac turpis egestas Cras id elit Integer quis urna Ut ante enim dapibus malesuada</p>
    <div class="btn" style="left:240px;top:118px;width:118px;height:30px;font-size:12px">READ MORE</div>
  </div>
</section>

<footer class="site-footer">
  <div class="contact-item" style="left:160px">
    <svg width="18" height="18" viewBox="0 0 24 24"><path d="M6.6 10.8a15 15 0 0 0 6.6 6.6l2.2-2.2a1 1 0 0 1 1-.25 11.4 11.4 0 0 0 3.6.57 1 1 0 0 1 1 1V20a1 1 0 0 1-1 1A17 17 0 0 1 3 4a1 1 0 0 1 1-1h3.5a1 1 0 0 1 1 1c0 1.25.2 2.45.57 3.57a1 1 0 0 1-.25 1z" fill="#fff"/></svg>
    1-555-014-2290</div>
  <div class="contact-item" style="left:378px">
    <svg width="16" height="20" viewBox="0 0 16 22"><path d="M8 0a8 8 0 0 0-8 8c0 6 8 14 8 14s8-8 8-14a8 8 0 0 0-8-8zm0 11a3 3 0 1 1 0-6 3 3 0 0 1 0 6z" fill="#fff"/></svg>
    4810 Lakeview Blvd, Suite 120, Avalon FL 30012</div>
  <div class="contact-item" style="left:856px">
    <svg width="18" height="14" viewBox="0 0 18 14"><rect width="18" height="14" rx="1" fill="#fff"/><path d="M1 1 L9 8 L17 1" stroke="#0a64bf" stroke-width="1.6" fill="none"/></svg>
    info@companyname.com</div>
  <div class="abs" style="left:116px;top:91px;width:968px;height:1px;background:rgba(255,255,255,.35)"></div>
  <nav class="foot-links">
    <a style="left:132px">HOME</a><a style="left:212px">ABOUT US</a><a style="left:320px">MORTGAGE 101</a><a style="left:462px">CONTACT US</a>
  </nav>
  <div class="social" style="left:934px"></div>
  <div class="social" style="left:972px"></div>
  <div class="social" style="left:1010px"></div>
  <div class="social" style="left:1048px"></div>
  <p class="abs" style="left:132px;top:146px;font-size:11px">© 2018 Company Name All right reserved</p>
  <p class="abs" style="left:132px;top:176px;font-size:12px;font-weight:700">Disclaimer</p>
  <p class="abs" style="left:132px;top:196px;width:950px;font-size:11.5px;line-height:19px">Licensed by the Bureau of Lending Affairs under the Pacific Credit Providers Act. Loans made or arranged pursuant to a Pacific Credit Providers Act License. Equal Housing Lender Brightwell Cannot Accept mortgage applications for properties located in New York via this site.</p>
</footer>

</body>
</html>
```